Velmora Consulting Business

** Please add the content information from my old business card
1. I would like to see a two sided business card with both options with the 1st Option--Tallow Spire-new WHITE BACKGROUND LOGO
2 nd Option-Tallow Spire - new BLACK- Background Logo
3rd -Option a business card with my Photo on the card
Please add the new word to the card information:
EXECUTION
AS THE OWNER'S REP
WE AIM TO ACHIEVE YOUR
INFRASTRUCTURE VISION with
OUR SPECIALIZATION & EXECUTION in:

FUNDING Planning
BUSINESS Planning
INFRASTRUCTURE Planning
PROJECT Management
Since 2012
_____________________________________________________________________
I want to get spot uv raised printing. I was liking a a nice rich white linen paper stock with black writing & NOT A COLORED CARD other than a variety of white or black cards concept

```html
<!DOCTYPE html>
<html lang="en">
<head>
<meta charset="utf-8">
<title>Velmora Consulting – Business Card Concepts</title>
<link href="https://fonts.googleapis.com/css2?family=Montserrat:wght@400;500;600;700&display=swap" rel="stylesheet">
<style>
  :root{
    --stage:#a9adab;
    --paper:#ffffff;
    --ink:#111111;
    --night:#050505;
    --red:#e31b3b;
    --text-light:#f4f4f4;
  }
  *{box-sizing:border-box;margin:0;padding:0}
  html,body{width:1200px;height:1118px;overflow:hidden;background:var(--stage)}
  body{position:relative;font-family:"Montserrat",Arial,sans-serif}
  .card{position:absolute;border-radius:18px;overflow:hidden}
  .card--white{background:var(--paper);color:var(--ink)}
  .card--black{background:var(--night);color:var(--text-light)}
  .abs{position:absolute}

  .brand{position:absolute;font-weight:600;line-height:1.05;letter-spacing:.5px}
  .brand span{display:block}
  .card--white .brand{color:var(--ink)}
  .card--black .brand{color:var(--text-light)}
  .brand-mark{position:absolute;width:12px;height:12px;background:var(--red)}

  .person-name{position:absolute;font-weight:700;color:var(--red);font-size:21px;white-space:nowrap}
  .person-title{position:absolute;font-size:13px;white-space:nowrap}
  .cities{position:absolute;font-size:13px;white-space:nowrap}
  .contacts{position:absolute;list-style:none;font-size:13px}
  .contacts li{display:flex;align-items:center;gap:12px;height:19.5px;white-space:nowrap}
  .contacts svg{width:12px;height:12px;flex:none}

  .divider{position:absolute;width:1.5px;background:var(--red)}
  .pitch{position:absolute;font-weight:700;color:var(--red);font-size:12.5px;line-height:17px;white-space:nowrap}
  .services{position:absolute;list-style:none;font-size:13.5px}
  .services li{white-space:nowrap}
  .services--plain li{height:23px}
  .services--bullets li{height:21.5px;display:flex;align-items:center;gap:7px}
  .services--bullets li::before{content:"";width:8px;height:8px;background:var(--red)}
  .since{position:absolute;font-size:13px}
</style>
</head>
<body>

<!-- Option 1: white front -->
<section class="card card--white" style="left:12px;top:15px;width:573px;height:342px">
  <div class="brand" style="left:28px;top:78px;font-size:30px"><span>Velmora</span><span>Consulting</span></div>
  <div class="brand-mark" style="left:28px;top:58px"></div>
  <div class="person-name" style="right:28px;top:36px">Rosalind Harker-Vance</div>
  <div class="person-title" style="right:28px;top:63px">CEO / LEAD PROJECT MANAGER</div>
  <div class="abs" style="right:0;top:38px;width:12px;height:39px;background:var(--red)"></div>
  <div class="abs" role="img" aria-label="Large red maple leaf decoration" style="left:362px;top:110px;width:211px;height:232px;background:radial-gradient(ellipse at 60% 55%,var(--red) 55%,rgba(227,27,59,0) 72%)"></div>
  <div class="cities" style="left:28px;top:220px">Tallow Bay NT · Ashcombe NB</div>
  <ul class="contacts" style="left:28px;top:262px">
    <li><svg viewBox="0 0 24 24"><path fill="var(--red)" d="M6.6 10.8a15.1 15.1 0 0 0 6.6 6.6l2.2-2.2a1 1 0 0 1 1-.25 11.4 11.4 0 0 0 3.6.57 1 1 0 0 1 1 1V20a1 1 0 0 1-1 1A17 17 0 0 1 3 4a1 1 0 0 1 1-1h3.5a1 1 0 0 1 1 1c0 1.25.2 2.45.57 3.570a1 1 0 0 1-.25 1z"/></svg>867.555.0182</li>
    <li><svg viewBox="0 0 24 24"><path fill="var(--red)" d="M2 5h20v14H2z M2 5l10 7 10-7" stroke="#fff" stroke-width="1.5"/></svg>ros@velmora.ca</li>
    <li><svg viewBox="0 0 24 24"><circle cx="12" cy="12" r="10" fill="var(--red)"/><path d="M2 12h20M12 2c3 3 3 17 0 20M12 2c-3 3-3 17 0 20" stroke="#fff" stroke-width="1.3" fill="none"/></svg>ww.velmora.ca</li>
  </ul>
</section>

<!-- Option 1: white back -->
<section class="card card--white" style="left:606px;top:15px;width:571px;height:350px">
  <div class="brand-mark" style="left:67px;top:150px"></div>
  <div class="brand" style="left:67px;top:170px;font-size:34px"><span>Velmora</span><span>Consulting</span></div>
  <div class="divider" style="left:292px;top:77px;height:206px"></div>
  <div class="pitch" style="left:316px;top:80px">AS THE OWNER'S REP<br>WE AIM TO ACHIEVE YOUR<br>INFRASTRUCTURE VISION with<br>OUR SPECIALIZATION in:</div>
  <ul class="services services--plain" style="left:316px;top:172px">
    <li>FUNDING Planning</li><li>BUSINESS Planning</li><li>INFRASTRUCTURE Planning</li><li>PROJECT Management</li><li>Since 2012</li>
  </ul>
</section>

<!-- Option 2: black front -->
<section class="card card--black" style="left:15px;top:398px;width:575px;height:344px">
  <div class="brand-mark" style="left:26px;top:50px"></div>
  <div class="brand" style="left:26px;top:70px;font-size:30px"><span>Velmora</span><span>Consulting</span></div>
  <div class="person-name" style="left:25px;top:171px">Rosalind Harker-Vance</div>
  <div class="person-title" style="left:25px;top:198px">CEO / LEAD PROJECT MANAGER</div>
  <div class="abs" style="left:27px;top:221px;width:501px;height:1.5px;background:var(--red)"></div>
  <ul class="contacts" style="left:28px;top:249px">
    <li><svg viewBox="0 0 24 24"><path fill="var(--red)" d="M6.6 10.8a15.1 15.1 0 0 0 6.6 6.6l2.2-2.2a1 1 0 0 1 1-.25 11.4 11.4 0 0 0 3.6.57 1 1 0 0 1 1 1V20a1 1 0 0 1-1 1A17 17 0 0 1 3 4a1 1 0 0 1 1-1h3.5a1 1 0 0 1 1 1c0 1.25.2 2.45.57 3.57a1 1 0 0 1-.25 1z"/></svg>867.555.0182</li>
    <li><svg viewBox="0 0 24 24"><path fill="var(--red)" d="M2 5h20v14H2z M2 5l10 7 10-7" stroke="#050505" stroke-width="1.5"/></svg>ros@velmora.ca</li>
    <li><svg viewBox="0 0 24 24"><circle cx="12" cy="12" r="10" fill="var(--red)"/><path d="M2 12h20M12 2c3 3 3 17 0 20M12 2c-3 3-3 17 0 20" stroke="#050505" stroke-width="1.3" fill="none"/></svg>ww.velmora.ca</li>
  </ul>
  <div class="cities" style="right:39px;top:282px">Tallow Bay NT · Ashcombe NB</div>
  <svg class="abs" style="left:0;bottom:0" width="575" height="12" viewBox="0 0 575 12">
    <polygon points="0,0 338,0 328,12 0,12" fill="var(--red)"/>
    <polygon points="342,0 575,0 575,12 332,12" fill="#fff"/>
  </svg>
</section>

<!-- Option 2: black back -->
<section class="card card--black" style="left:614px;top:401px;width:566px;height:340px">
  <div class="brand-mark" style="left:66px;top:150px"></div>
  <div class="brand" style="left:66px;top:170px;font-size:34px"><span>Velmora</span><span>Consulting</span></div>
  <div class="divider" style="left:290px;top:88px;height:162px"></div>
  <div class="pitch" style="left:314px;top:84px">AS THE OWNER'S REP<br>WE AIM TO ACHIEVE YOUR<br>INFRASTRUCTURE VISION with<br>OUR SPECIALIZATION in:</div>
  <ul class="services services--bullets" style="left:311px;top:167px">
    <li>FUNDING Planning</li><li>BUSINESS Planning</li><li>INFRASTRUCTURE Planning</li><li>PROJECT Management</li>
  </ul>
  <div class="since" style="right:33px;top:288px">Since 2012</div>
</section>

<!-- Option 3: photo front -->
<section class="card card--black" style="left:24px;top:757px;width:573px;height:342px;background:#0b0b0c">
  <div class="abs" role="img" aria-label="Portrait photo of the CEO" style="left:0;top:0;width:230px;height:342px;background:linear-gradient(180deg,#6e4a33 0%,#3a2a22 45%,#141414 100%)"></div>
  <div class="brand-mark" style="left:266px;top:42px"></div>
  <div class="brand" style="left:266px;top:62px;font-size:30px"><span>Velmora</span><span>Consulting</span></div>
  <div class="person-name" style="left:269px;top:181px">Rosalind Harker-Vance</div>
  <div class="person-title" style="left:269px;top:208px">CEO / LEAD PROJECT MANAGER</div>
  <div class="cities" style="left:269px;top:236px">Tallow Bay NT · Ashcombe NB</div>
  <ul class="contacts" style="left:269px;top:258px">
    <li><svg viewBox="0 0 24 24"><path fill="var(--red)" d="M6.6 10.8a15.1 15.1 0 0 0 6.6 6.6l2.2-2.2a1 1 0 0 1 1-.25 11.4 11.4 0 0 0 3.6.57 1 1 0 0 1 1 1V20a1 1 0 0 1-1 1A17 17 0 0 1 3 4a1 1 0 0 1 1-1h3.5a1 1 0 0 1 1 1c0 1.25.2 2.45.57 3.57a1 1 0 0 1-.25 1z"/></svg>867.555.0182</li>
    <li><svg viewBox="0 0 24 24"><path fill="var(--red)" d="M2 5h20v14H2z M2 5l10 7 10-7" stroke="#0b0b0c" stroke-width="1.5"/></svg>ros@velmora.ca</li>
    <li><svg viewBox="0 0 24 24"><circle cx="12" cy="12" r="10" fill="var(--red)"/><path d="M2 12h20M12 2c3 3 3 17 0 20M12 2c-3 3-3 17 0 20" stroke="#0b0b0c" stroke-width="1.3" fill="none"/></svg>ww.velmora.ca</li>
  </ul>
</section>

<!-- Option 3: back -->
<section class="card card--black" style="left:623px;top:760px;width:557px;height:332px">
  <div class="brand-mark" style="left:66px;top:146px"></div>
  <div class="brand" style="left:66px;top:166px;font-size:34px"><span>Velmora</span><span>Consulting</span></div>
  <div class="divider" style="left:285px;top:87px;height:158px"></div>
  <div class="pitch" style="left:309px;top:83px">AS THE OWNER'S REP<br>WE AIM TO ACHIEVE YOUR<br>INFRASTRUCTURE VISION with<br>OUR SPECIALIZATION in:</div>
  <ul class="services services--bullets" style="left:306px;top:163px">
    <li>FUNDING Planning</li><li>BUSINESS Planning</li><li>INFRASTRUCTURE Planning</li><li>PROJECT Management</li>
  </ul>
  <div class="since" style="right:32px;top:283px">Since 2012</div>
</section>

</body>
</html>
```